Fresh Dwelling Tract Guide needs a new Landing Page

I like to get a landing page or website with 2-3 pages to help target home buyers who are looking to buy homes from builders such as TW Residences, Morvik, P.L. Fennick, etc. The landing page/website to be non-cluttered and be able to explain to home buyers that there are many benefits to include me as their buyer's agent when they buy a brand new home from any builders.
I may want to incorporate a short explanation video (animated) on the landing page and then for the viewer to click on a button that will take them to another page where they can search for new homes from different builders.
Target Market(s)
Home buyers looking to buy brand new home from builders such as TW Residences, Morvik, P.L. Fennick, etc.
Industry/Entity Type
Real Estate
Number of Pages Required
2 page
Font styles to use
Requirements
Must have
- The landing page may have the explanation video at the bottom of the landing page (scrolled down) or there may be a CALL TO ACTION button that takes the viewer to the 2nd page to watch the explanation video. Once they watched the explanation video and are still interested, they can click on another CALL TO ACTION button that will take them to another website that they will be able to search for all the available new homes and register their contact information.
Should not have
- No clutters and no dark colors.

```html
<!DOCTYPE html>
<html lang="en">
<head>
<meta charset="utf-8">
<title>Fresh Dwelling Tract Guide</title>
<link rel="stylesheet" href="https://fonts.googleapis.com/css2?family=Kaushan+Script&family=Lora:ital,wght@0,400;0,500;1,400&family=Open+Sans:wght@400;600;700&display=swap">
<style>
:root{
  --green:#a5b63b;
  --brown:#4b3a2c;
  --ink:#3b3b3b;
  --muted:#8a8a8a;
  --band:#f3f3f3;
  --line:#e6e6e6;
  --link:#4a90c8;
  --white:#ffffff;
}
*{margin:0;padding:0;box-sizing:border-box}
html,body{width:1200px;height:4327px;overflow:hidden;background:var(--white)}
body{position:relative;font-family:"Open Sans",sans-serif;color:var(--ink)}
.abs{position:absolute}
.brand{display:flex;align-items:center;gap:12px;font-family:"Lora",serif;font-size:26px;color:var(--brown)}
.brand-dot{width:26px;height:26px;border-radius:50%;background:var(--green)}
.menu{left:1035px;top:52px;display:flex;align-items:center;gap:10px;font-size:13px;font-weight:600;color:var(--green);letter-spacing:1px}
.script{font-family:"Kaushan Script",cursive;color:var(--brown)}
.serif{font-family:"Lora",serif}
.btn{display:flex;align-items:center;justify-content:center;background:var(--green);color:var(--white);font-size:13px;font-weight:700;letter-spacing:2px;text-transform:uppercase}
.play{display:flex;align-items:center;gap:14px;font-size:16px;font-weight:600;color:var(--ink)}
.band{left:0;width:1200px;background:var(--band)}
.partner{font-family:"Lora",serif;font-size:30px;color:var(--brown)}
.label{font-family:"Lora",serif;font-size:22px;letter-spacing:1px;color:var(--ink)}
.card-img{width:490px;height:294px}
.card-title{font-family:"Lora",serif;font-size:22px;color:var(--ink)}
.meta{font-size:10px;color:var(--muted);letter-spacing:1px}
.excerpt{font-size:14px;line-height:1.45;color:#555;width:490px}
.more{font-size:13px;color:var(--link);letter-spacing:1px}
.field{width:432px;height:58px;border:1px solid var(--line);box-shadow:0 2px 6px rgba(0,0,0,.05);font-size:12px;color:#aaa;padding:18px 24px}
.small{font-size:14px;line-height:1.55;color:#555}
</style>
</head>
<body>

<header>
  <div class="abs brand" style="left:87px;top:78px"><span class="brand-dot"></span>Parkside Home Walk</div>
  <div class="abs menu">MENU
    <svg width="30" height="22" viewBox="0 0 30 22"><g stroke="#a5b63b" stroke-width="2.5"><line x1="0" y1="3" x2="30" y2="3"/><line x1="0" y1="11" x2="30" y2="11"/><line x1="0" y1="19" x2="30" y2="19"/></g></svg>
  </div>
</header>

<section class="hero">
  <h1 class="abs script" style="left:87px;top:205px;font-size:88px;font-weight:400">Find your home today</h1>
  <p class="abs serif" style="left:87px;top:313px;font-size:35px;color:var(--brown)">Get the service you deserved</p>
  <a class="abs btn" style="left:87px;top:400px;width:181px;height:53px">Find a home</a>
  <div class="abs play" style="left:87px;top:502px">See how it works
    <svg width="44" height="44" viewBox="0 0 44 44"><circle cx="22" cy="22" r="20" fill="none" stroke="#333" stroke-width="2.5"/><path d="M17 13 L31 22 L17 31Z" fill="#333"/></svg>
  </div>
</section>

<section class="abs band" style="top:649px;height:280px">
  <h2 class="abs serif" style="left:0;width:1200px;text-align:center;top:54px;font-size:34px;font-weight:400;color:var(--brown)">Buy a brand new home from any builders like</h2>
  <div class="abs" style="left:210px;top:147px;width:70px;height:70px;border-radius:50%;background:#d9b44a" role="img" aria-label="Partner anniversary badge"></div>
  <div class="abs" style="left:304px;top:144px;width:1px;height:76px;background:#aaa"></div>
  <div class="abs partner" style="left:322px;top:162px">P.L. Fennick</div>
  <div class="abs partner" style="left:588px;top:162px">TW Residences</div>
  <div class="abs partner" style="left:880px;top:162px">Morvik</div>
</section>

<section class="blog">
  <h3 class="abs label" style="left:87px;top:990px;font-weight:400">BLOG</h3>
  <div class="abs card-img" style="left:87px;top:1082px;background:linear-gradient(180deg,#5cc3e0 0%,#5cc3e0 30%,#d9727f 60%,#d66a78 100%)" role="img" aria-label="Pink house gable against a blue sky"></div>
  <h4 class="abs card-title" style="left:87px;top:1393px;font-weight:400">Open House Weekend Report: September 21-23</h4>
  <p class="abs meta" style="left:87px;top:1442px">BY ADMIN | HOMES | 09.23</p>
  <p class="abs excerpt" style="left:87px;top:1472px">Get up close and personal with Halbrook during one of our favorite home tours in New York City, the Hamptons, and South Florida.</p>
  <a class="abs more" style="left:87px;top:1535px">READ MORE</a>

  <div class="abs card-img" style="left:623px;top:1082px;background:linear-gradient(135deg,#5d7a3e 0%,#c9c4b8 50%,#4e6b34 100%)" role="img" aria-label="Aerial view of homes surrounded by park greenery"></div>
  <h4 class="abs card-title" style="left:623px;top:1393px;font-weight:400">6 Homes with Incredible Park Views</h4>
  <p class="abs meta" style="left:623px;top:1442px">BY ADMIN | HOMES | 09.18</p>
  <p class="abs excerpt" style="left:623px;top:1472px">There's no better spot to watch the leaves change this foliage season than your own home!</p>
  <a class="abs more" style="left:623px;top:1535px">READ MORE</a>

  <a class="abs btn" style="left:508px;top:1621px;width:184px;height:52px">View more</a>
</section>

<section class="abs band" style="top:1742px;height:476px">
  <h2 class="abs serif" style="left:0;width:1200px;text-align:center;top:82px;font-size:34px;font-weight:400;color:var(--brown)">Success Stories</h2>
  <svg class="abs" style="left:83px;top:222px" width="24" height="36" viewBox="0 0 24 36"><path d="M20 3 L5 18 L20 33" fill="none" stroke="#a5b63b" stroke-width="4"/></svg>
  <svg class="abs" style="left:1092px;top:222px" width="24" height="36" viewBox="0 0 24 36"><path d="M4 3 L19 18 L4 33" fill="none" stroke="#a5b63b" stroke-width="4"/></svg>
  <div class="abs" style="left:175px;top:153px;width:174px;height:174px;border-radius:50%;background:linear-gradient(160deg,#8a8a8a,#3c3c3c);box-shadow:0 4px 12px rgba(0,0,0,.15)" role="img" aria-label="Portrait of the client"></div>
  <div class="abs serif" style="left:430px;top:160px;font-size:64px;color:var(--brown);line-height:1">&ldquo;</div>
  <p class="abs serif" style="left:433px;top:226px;width:660px;font-size:24px;font-style:italic;line-height:1.4;color:var(--brown)">Lorem ipsum dolor sit amet, consectetur adipisicing elit, sed do eiusmod</p>
  <p class="abs" style="left:433px;top:333px;font-size:14px;color:#555"><b>Mira Caldwell</b>, VP of Global Marketing, Lunaveta</p>
</section>

<section class="cta">
  <h2 class="abs script" style="left:0;width:1200px;text-align:center;top:2310px;font-size:86px;font-weight:400">Find your home today</h2>
  <a class="abs btn" style="left:508px;top:2461px;width:184px;height:52px">Find a home</a>
  <div class="abs play" style="left:490px;top:2554px">Watch how it works
    <svg width="44" height="44" viewBox="0 0 44 44"><circle cx="22" cy="22" r="20" fill="none" stroke="#333" stroke-width="2.5"/><path d="M17 13 L31 22 L17 31Z" fill="#333"/></svg>
  </div>
</section>

<section class="contact">
  <h3 class="abs label" style="left:87px;top:2712px;font-weight:400">GET IN TOUCH</h3>
  <p class="abs small" style="left:87px;top:2770px;width:470px">We're always available to help out, get in touch with us any time, or shoot us an email.</p>
  <div class="abs field" style="left:87px;top:2873px">First Name</div>
  <div class="abs field" style="left:87px;top:2959px">Last Name</div>
  <div class="abs field" style="left:87px;top:3046px">Email Address</div>
  <div class="abs field" style="left:87px;top:3133px">Phone Number</div>
  <div class="abs field" style="left:87px;top:3220px;height:178px">Questions/Comments</div>
  <a class="abs btn" style="left:87px;top:3502px;width:432px;height:52px">Submit</a>

  <div class="abs" style="left:641px;top:2732px;width:80px;height:80px;border-radius:50%;background:linear-gradient(160deg,#c9b89c,#4f4336)" role="img" aria-label="Portrait of the agent"></div>
  <p class="abs serif" style="left:759px;top:2732px;font-size:22px;color:var(--brown)">Your Name</p>
  <p class="abs" style="left:759px;top:2780px;font-size:13px;color:#555">CalDRE License # 01234567</p>
  <div class="abs" style="left:759px;top:2816px;display:flex;align-items:center;gap:14px;font-size:13px;color:#555">
    <svg width="14" height="14" viewBox="0 0 24 24"><path d="M6.6 10.8a15 15 0 0 0 6.6 6.6l2.2-2.2c.3-.3.7-.4 1-.2 1.1.4 2.3.6 3.6.6.6 0 1 .4 1 1V20c0 .6-.4 1-1 1A17 17 0 0 1 3 4c0-.6.4-1 1-1h3.5c.6 0 1 .4 1 1 0 1.3.2 2.5.6 3.6.1.3 0 .7-.2 1z" fill="#444"/></svg>555.010.2468
  </div>
  <div class="abs" style="left:759px;top:2851px;display:flex;align-items:center;gap:14px;font-size:13px;color:#555">
    <svg width="14" height="12" viewBox="0 0 24 20"><rect x="1" y="1" width="22" height="18" rx="2" fill="#444"/><path d="M2 3 L12 11 L22 3" fill="none" stroke="#fff" stroke-width="2"/></svg>email me
  </div>
</section>

<footer>
  <div class="abs" style="left:0;top:3687px;width:1200px;height:1px;background:var(--line)"></div>
  <h3 class="abs label" style="left:87px;top:3780px;font-weight:400">ABOUT US</h3>
  <p class="abs small" style="left:87px;top:3840px;width:470px">Lorem ipsum dolor sit amet, consectetur adipisicing elit, sed do eiusmod incididunt ut labore et dolore magna aliqua. Ut enim ad minim veniam.</p>
  <p class="abs small" style="left:87px;top:3925px;width:470px">Lorem ipsum dolor sit amet, consectetur adipisicing elit, sed do eiusmod tempor incididunt ut labore et dolore magna aliqua. Ut enim ad minim veniam, quis nostrud exercitation ullamco laboris nisi ut aliquip ex ea commodo consequat.</p>
  <a class="abs more" style="left:87px;top:4065px;letter-spacing:0">Email us</a>
  <div class="abs brand" style="left:87px;top:4160px"><span class="brand-dot"></span>Parkside Home Walk</div>

  <div class="abs" style="left:600px;top:3765px;width:1px;height:410px;background:#cfcfcf"></div>

  <h3 class="abs label" style="left:690px;top:3780px;font-weight:400">GET UPDATES</h3>
  <div class="abs field" style="left:690px;top:3846px;width:421px;height:54px">Your Email</div>
  <a class="abs btn" style="left:690px;top:3938px;width:164px;height:55px">Sign up</a>
</footer>

</body>
</html>
```